Business card design for holistic health care clinic

We need a double-sided business card design for our holistic health care clinic that integrates our logo design and also its color scheme. My business is called Valmira. It is an integrative medicine clinic. You have already done the logo for me. Please ensure an elegant and upscale design that is not cluttered, but still has all the necessary information (please see below for details).

Target Market(s)

Wellness, fitness, rehabilitation for educated, well-traveled open-minded clients who are focused on natural, organic, balanced and preventive healthcare and lifestyle.

Industry/Entity Type

Medical

Contact Information for Business Card

Modern, clean.

Number of Pages Required

1 page

Font styles to use
Serif
Sans Serif

Colors

Designer to choose colors to be used in the design.

Requirements
Must have
• Logo on one side, all other information on the other side.
• Other information should include:
• Tobias Wrenfeld - DOE, CPT, LMT
• 4100 East Marrow Drive
• Austin, TX 78119
• 512 555 0148
• 818 555 0192
• info@ValmiraHealth.example
• t.wrenfeld@ValmiraHealth.example
Nice to have
• Darker background on front - but not totally black - shaded/dark gray.

```html
<!DOCTYPE html>
<html lang="en">
<head>
<meta charset="utf-8">
<title>Valmira – Business Card</title>
<link rel="stylesheet" href="https://fonts.googleapis.com/css2?family=Open+Sans:wght@400;600;700&display=swap">
<style>
  :root {
    --backdrop: #e9e7e4;
    --panel-deep: #0f4f8c;
    --panel-mid: #2a78bd;
    --panel-light: #5aa0d6;
    --frost: #dcdad6;
    --frost-light: #eeede9;
    --ink-light: #f3f6fa;
    --brand-navy: #14467f;
    --brand-blue: #1f5ea6;
  }
  * { box-sizing: border-box; margin: 0; padding: 0; }
  html, body {
    width: 1200px;
    height: 969px;
    overflow: hidden;
    background: var(--backdrop);
    font-family: "Open Sans", Arial, sans-serif;
  }
  .card {
    position: absolute;
    left: 100px;
    top: 200px;
    width: 1000px;
    height: 570px;
    display: flex;
    background: linear-gradient(160deg, var(--frost-light), var(--frost));
    box-shadow: 0 14px 40px rgba(0,0,0,0.18);
    overflow: hidden;
  }
  .contact-panel {
    width: 466px;
    height: 100%;
    padding: 160px 0 0 52px;
    background: linear-gradient(115deg, var(--panel-deep) 0%, var(--panel-mid) 55%, var(--panel-light) 100%);
    color: var(--ink-light);
  }
  .holder-name {
    font-size: 26px;
    font-weight: 700;
    letter-spacing: 0.5px;
    text-transform: uppercase;
  }
  .holder-name .credentials {
    font-size: 16px;
    font-weight: 700;
    letter-spacing: 0.3px;
  }
  .address {
    margin-top: 22px;
    font-size: 23px;
    line-height: 38px;
  }
  .contact-list {
    list-style: none;
    margin-top: 30px;
    font-size: 21px;
    line-height: 33px;
  }
  .contact-list li {
    display: flex;
    align-items: center;
    gap: 14px;
  }
  .contact-list svg {
    width: 18px;
    height: 18px;
    flex: none;
    fill: var(--ink-light);
  }
  .brand-side {
    flex: 1;
    display: flex;
    flex-direction: column;
    align-items: center;
    justify-content: center;
    padding-bottom: 20px;
  }
  .brand-name {
    font-size: 84px;
    font-weight: 700;
    color: var(--brand-navy);
    letter-spacing: 1px;
    line-height: 1;
    text-transform: uppercase;
  }
  .brand-tagline {
    margin-top: 12px;
    font-size: 27px;
    font-weight: 600;
    color: var(--brand-blue);
  }
</style>
</head>
<body>
  <div class="card">
    <section class="contact-panel">
      <h1 class="holder-name">Tobias Wrenfeld <span class="credentials">- DOE, CPT, LMT</span></h1>
      <p class="address">4100 East Marrow Drive<br>Austin, TX 78119</p>
      <ul class="contact-list">
        <li>
          <svg viewBox="0 0 24 24" aria-hidden="true"><path d="M3 8c0-3 4-5 9-5s9 2 9 5v2h-5V8H8v2H3z"/><rect x="5" y="12" width="14" height="9" rx="2"/></svg>
          512 555 0148
        </li>
        <li>
          <svg viewBox="0 0 24 24" aria-hidden="true"><path d="M7 1h10a2 2 0 0 1 2 2v18a2 2 0 0 1-2 2H7a2 2 0 0 1-2-2V3a2 2 0 0 1 2-2zm0 3v14h10V4z"/></svg>
          818 555 0192
        </li>
        <li>
          <svg viewBox="0 0 24 24" aria-hidden="true"><path d="M2 5h20v14H2z" opacity="0.35"/><path d="M2 5h20v2l-10 7L2 7zM2 9l10 7 10-7v10H2z"/></svg>
          t.wrenfeld@ValmiraHealth.example
        </li>
        <li>
          <svg viewBox="0 0 24 24" aria-hidden="true"><circle cx="12" cy="12" r="10"/><path d="M12 2v20M2 12h20" stroke="#2a78bd" stroke-width="1.6" fill="none"/></svg>
          www.ValmiraHealth.example
        </li>
      </ul>
    </section>
    <section class="brand-side">
      <div class="brand-name">Valmira</div>
      <div class="brand-tagline">Integrative Holistic Medicine</div>
    </section>
  </div>
</body>
</html>
```